Progressive European Honey Business needs minimalistic packaging design

Hello - thank you for your interest in our brief. We are Honey Plinks, a London based Honey business, importing only the best honey Europe has to offer. Our values are deeply rooted with in progressive liberal values and we are looking for minimalist packaging, which reflects that.

We are looking for a design, which dimensions fit with our packaging option (Vessio Glass Jar | HEIGHT 90mm | DIAMETER 63mm). We will require a various output files (High Resolution JPEG (CMYK Colors 300 dpi) Source File Ai, PSD, PDF, Printing files (die cut, die folding) and a 3D Mockup of the packaging for use within digital commerce platforms.

We must be able to adjust the free text on the label front and it should include the following:
Brand Name
Honey type
Limited edition No. X / 100 ( X being the number of purchase i.e. 25 / 100)
EU Honey, Single Orgin (Germany)
(c) The net weight (250g)

The back must include room for additional information (again adjustable by us) and the following:
“Unsuitable for children under 12 months”
(b) The appropriate durability declaration

In total, we are looking for
a) A front label
b) A back label
c) A seal (round) including the attached bee and logo included in the Zip file.
Do note that a) & b) can also be combined into one design as long as the symmetry on the jar stays intact.

The final design should communicate modern aesthetics, high quality, that are slightly provocative and pop off the shelves.

Hi folks, sorry for the delay in completing this project, but my business partner had a leak in his house. We planned to finalise our review today, but this will have to wait until it's no longer raining in his livingroom. Our sincere apologies!

• See branding guidelines

• Must follow the branding guideline and fonts provided as attachment

```html
<!DOCTYPE html>
<html lang="en">
<head>
<meta charset="utf-8">
<title>Honey Plinks – Front Label</title>
<link href="https://fonts.googleapis.com/css2?family=Ultra&family=Poppins:wght@300;400;600;700;800&display=swap" rel="stylesheet">
<style>
  :root {
    --page: #ffffff;
    --label: #ececec;
    --label-light: #f4f4f4;
    --comb: #e2e2e2;
    --brand-orange: #e5652a;
    --seal-yellow: #f6c21c;
    --ink: #1e1e1e;
    --plum: #6e2a86;
    --band: #222222;
    --band-text: #ffffff;
  }
  * { margin: 0; padding: 0; box-sizing: border-box; }
  html, body {
    width: 1200px;
    height: 1200px;
    overflow: hidden;
    background: var(--page);
  }
  .canvas {
    position: relative;
    width: 1200px;
    height: 1200px;
    display: flex;
    align-items: center;
    justify-content: center;
  }
  .front-label {
    position: relative;
    width: 1040px;
    height: 760px;
    background: var(--label);
    overflow: hidden;
  }
  .comb-backdrop {
    position: absolute;
    inset: 0 0 140px 0;
    background: radial-gradient(ellipse at 50% 40%, var(--label-light) 0%, var(--label) 55%, var(--comb) 100%);
  }
  .brand {
    position: absolute;
    top: 70px;
    left: 0;
    right: 0;
    display: flex;
    flex-direction: column;
    align-items: center;
    gap: 26px;
  }
  .brand-mark {
    width: 150px;
    height: 150px;
    border-radius: 50%;
    background: var(--seal-yellow);
  }
  .brand-name {
    font-family: 'Poppins', sans-serif;
    font-weight: 800;
    font-size: 46px;
    letter-spacing: 1px;
    color: var(--brand-orange);
    text-transform: uppercase;
    line-height: 1;
  }
  .honey-type {
    position: absolute;
    top: 348px;
    left: 0;
    right: 0;
    text-align: center;
    font-family: 'Ultra', serif;
    font-size: 118px;
    line-height: 1;
    color: var(--ink);
    letter-spacing: -2px;
    text-transform: uppercase;
  }
  .origin {
    position: absolute;
    top: 500px;
    left: 0;
    right: 0;
    text-align: center;
    font-family: 'Poppins', sans-serif;
    text-transform: uppercase;
  }
  .origin-region {
    font-weight: 700;
    font-size: 32px;
    color: var(--plum);
    line-height: 1;
  }
  .origin-country {
    margin-top: 18px;
    font-weight: 300;
    font-size: 28px;
    color: var(--ink);
    line-height: 1;
  }
  .info-band {
    position: absolute;
    left: 0;
    right: 0;
    top: 620px;
    height: 96px;
    background: var(--band);
    display: flex;
    align-items: center;
    justify-content: center;
    gap: 56px;
    font-family: 'Poppins', sans-serif;
    font-size: 26px;
    color: var(--band-text);
    text-transform: uppercase;
  }
  .net-weight { font-weight: 600; }
  .divider { font-weight: 300; }
  .edition { font-weight: 300; }
</style>
</head>
<body>
  <main class="canvas">
    <section class="front-label">
      <div class="comb-backdrop" role="img" aria-label="Faint honeycomb pattern across the label background"></div>

      <header class="brand">
        <span class="brand-mark"></span>
        <h1 class="brand-name">Honey Plinks</h1>
      </header>

      <h2 class="honey-type">Honey Type</h2>

      <div class="origin">
        <p class="origin-region">EU Honey</p>
        <p class="origin-country">Single Orgin Germany</p>
      </div>

      <footer class="info-band">
        <span class="net-weight">Net Weight (250g)</span>
        <span class="divider">|</span>
        <span class="edition">Limited Edition No. X/100</span>
      </footer>
    </section>
  </main>
</body>
</html>
```